New Business Card Design Project

Need a design that will create an impact / strong impression towards our clients for our business. We are in the lighting business and we do lighting retrofits for large commercial to industrial clientele.

Target Market(s)

Lighting Industry

Industry/Entity Type

Business

Font styles to use
Other font styles liked:
• we would like to use the font on our logo, not sure what it is though..

Requirements
Must have
• Our logo.
Nice to have
• We are open to suggestions that have to do with lighting.

```html
<!DOCTYPE html>
<html lang="en">
<head>
<meta charset="utf-8">
<title>Brightline Retrofit Group – Business Card</title>
<link href="https://fonts.googleapis.com/css2?family=Montserrat:wght@800&family=Open+Sans:wght@400;600&display=swap" rel="stylesheet">
<style>
  :root {
    --canvas-bg: #d4d4d4;
    --card-white: #ffffff;
    --brand-dark: #1e3a1e;
    --brand-green: #1f8a3c;
    --brand-light: #56b849;
    --text-grey: #7a7a7a;
  }
  * { box-sizing: border-box; margin: 0; padding: 0; }
  html, body { width: 1200px; height: 800px; overflow: hidden; }
  body {
    background: var(--canvas-bg);
    font-family: "Open Sans", Arial, sans-serif;
    display: flex;
    flex-direction: column;
    align-items: center;
    justify-content: center;
    gap: 40px;
  }
  .card {
    width: 520px;
    height: 297px;
    position: relative;
    overflow: hidden;
    box-shadow: 0 6px 18px rgba(0,0,0,0.18);
  }
  .brand-lockup {
    position: absolute;
    left: 0; right: 0;
    padding: 0 30px;
    display: flex;
    justify-content: center;
    align-items: center;
    gap: 10px;
  }
  .brand-name {
    font-family: "Montserrat", Arial, sans-serif;
    font-weight: 800;
    letter-spacing: 0.5px;
    text-transform: uppercase;
    white-space: nowrap;
  }
  .brand-square { flex: none; width: 16px; height: 16px; }

  /* Front */
  .card-front {
    background: var(--card-white);
    border-bottom: 6px solid var(--brand-green);
  }
  .card-front .brand-lockup { top: 52px; }
  .card-front .brand-name { color: var(--brand-green); font-size: 21px; }
  .card-front .brand-square { background: var(--brand-light); }
  .identity-row {
    position: absolute;
    top: 128px;
    left: 0; right: 0;
    display: flex;
    justify-content: center;
    align-items: center;
    gap: 22px;
  }
  .person { text-align: right; }
  .person-name {
    color: var(--brand-green);
    font-size: 17px;
    font-weight: 400;
    text-transform: uppercase;
    letter-spacing: 0.3px;
    white-space: nowrap;
  }
  .person-title { color: var(--text-grey); font-size: 14px; }
  .divider {
    width: 2px; height: 62px;
    background: var(--brand-light);
  }
  .contact-list { list-style: none; }
  .contact-list li {
    display: flex; align-items: center; gap: 8px;
    color: var(--text-grey);
    font-size: 11.5px;
    line-height: 20px;
    white-space: nowrap;
  }
  .contact-list svg { width: 10px; height: 10px; fill: var(--brand-green); flex: none; }
  .address {
    position: absolute;
    bottom: 44px;
    left: 0; right: 0;
    text-align: center;
    color: var(--text-grey);
    font-size: 12.5px;
    white-space: nowrap;
  }

  /* Back */
  .card-back { background: var(--brand-dark); }
  .card-back .brand-lockup { top: 130px; gap: 12px; }
  .card-back .brand-name { color: #ffffff; font-size: 22px; }
  .card-back .brand-square { background: #ffffff; width: 18px; height: 18px; }
  .card-back .web {
    position: absolute;
    right: 34px;
    bottom: 28px;
    color: #ffffff;
    font-size: 11px;
    letter-spacing: 1px;
    white-space: nowrap;
  }
</style>
</head>
<body>
  <section class="card card-front" aria-label="Business card front">
    <div class="brand-lockup">
      <span class="brand-name">Brightline Retrofit Group, LLC</span>
      <span class="brand-square"></span>
    </div>
    <div class="identity-row">
      <div class="person">
        <p class="person-name">Daniel Reyes</p>
        <p class="person-title">Founder</p>
      </div>
      <div class="divider"></div>
      <ul class="contact-list">
        <li><svg viewBox="0 0 10 10"><path d="M2 0.5l1.8 2-1 1.2a6 6 0 0 0 3.5 3.5l1.2-1 2 1.8-1.3 1.5C4.5 9.5 0.5 5.5 0.5 1.8z"/></svg>0400 555 017</li>
        <li><svg viewBox="0 0 10 10"><path d="M0.5 2h9v6h-9z M0.5 2l4.5 3.5L9.5 2"/></svg>info@brightlinegroup.com</li>
        <li><svg viewBox="0 0 10 10"><circle cx="5" cy="5" r="4.5"/></svg>www.brightlinegroup.com</li>
      </ul>
    </div>
    <p class="address">4820 West Harbor Road, Suite C204 Tempe AZ 85281</p>
  </section>

  <section class="card card-back" aria-label="Business card back">
    <div class="brand-lockup">
      <span class="brand-name">Brightline Retrofit Group, LLC</span>
      <span class="brand-square"></span>
    </div>
    <p class="web">www.brightlinegroup.com</p>
  </section>
</body>
</html>
```